BOLD & MINIMALIST DESIGN NEEDED

We want a very bold but minimalistic business card design that is impactful and utilizes both sides of the business card. Our current logo is included for your use.

We want bold fonts and good use of negative space. We don't want the logo to overpower the design.

Target Market(s)

Professionals who are building new commercial buildings.

Industry/Entity Type

Construction

Contact Information for Business Card

Name, Title, email, office phone, cell phone, website

Font styles to use
Serif
Sans Serif

Requirements
Must have
• Bold design!

```html
<!DOCTYPE html>
<html lang="en">
<head>
<meta charset="UTF-8">
<title>Summitway Design + Build — Business Card</title>
<link href="https://fonts.googleapis.com/css2?family=Montserrat:wght@700;800&family=Roboto:wght@500&display=swap" rel="stylesheet">
<style>
  :root {
    --backdrop: #dfe4e2;
    --card: #ffffff;
    --ink: #111111;
    --text-grey: #555555;
    --brand-green: #7cc242;
    --rule: #222222;
  }
  * { margin: 0; padding: 0; box-sizing: border-box; }
  html, body {
    width: 1200px;
    height: 716px;
    overflow: hidden;
    background: var(--backdrop);
  }
  .canvas {
    position: relative;
    width: 1200px;
    height: 716px;
  }
  .card {
    position: absolute;
    left: 369px;
    width: 461px;
    height: 263px;
    background: var(--card);
    border-radius: 14px;
    box-shadow: 0 2px 6px rgba(0, 0, 0, 0.12);
  }
  .card--front { top: 94px; }
  .card--back  { top: 382px; }

  /* Wordmark */
  .wordmark {
    position: absolute;
    display: flex;
    align-items: center;
    font-family: "Montserrat", sans-serif;
    font-weight: 800;
    color: var(--ink);
    text-transform: uppercase;
  }
  .wordmark__square {
    background: var(--brand-green);
    flex-shrink: 0;
  }
  .wordmark__name { line-height: 1.05; }
  .wordmark__tag { display: block; letter-spacing: 0.32em; }

  .card--front .wordmark {
    left: 0; right: 0;
    top: 92px;
    justify-content: center;
    gap: 14px;
  }
  .card--front .wordmark__square { width: 50px; height: 50px; }
  .card--front .wordmark__name { font-size: 34px; }
  .card--front .wordmark__tag { font-size: 13px; margin-top: 4px; }

  .card--back .wordmark {
    left: 40px;
    top: 110px;
    gap: 8px;
  }
  .card--back .wordmark__square { width: 28px; height: 28px; }
  .card--back .wordmark__name { font-size: 19px; }
  .card--back .wordmark__tag { font-size: 8px; margin-top: 3px; }

  /* Contact block */
  .divider {
    position: absolute;
    left: 231px;
    top: 64px;
    width: 1.5px;
    height: 135px;
    background: var(--rule);
  }
  .contact {
    position: absolute;
    left: 245px;
    top: 63px;
    color: var(--text-grey);
  }
  .contact__name {
    font-family: "Montserrat", sans-serif;
    font-weight: 700;
    font-size: 15.5px;
    line-height: 1.15;
  }
  .contact__title {
    font-family: "Montserrat", sans-serif;
    font-weight: 700;
    font-size: 11.5px;
    margin-top: 2px;
  }
  .contact__list {
    list-style: none;
    font-family: "Roboto", sans-serif;
    font-weight: 500;
    font-size: 12.5px;
    line-height: 16.5px;
  }
  .contact__list--reach { margin-top: 12px; }
  .contact__list--address { margin-top: 12px; }
</style>
</head>
<body>
<main class="canvas">

  <section class="card card--front" aria-label="Card front">
    <div class="wordmark">
      <span class="wordmark__square" aria-hidden="true"></span>
      <span class="wordmark__name">Summitway<span class="wordmark__tag">Design + Build</span></span>
    </div>
  </section>

  <section class="card card--back" aria-label="Card back">
    <div class="wordmark">
      <span class="wordmark__square" aria-hidden="true"></span>
      <span class="wordmark__name">Summitway<span class="wordmark__tag">Design + Build</span></span>
    </div>

    <span class="divider" aria-hidden="true"></span>

    <div class="contact">
      <p class="contact__name">Maren Holt</p>
      <p class="contact__title">Designer</p>
      <ul class="contact__list contact__list--reach">
        <li>P : +123-45-67890</li>
        <li>E : info@youremail.com</li>
        <li>W : www.infoweibsite.com</li>
      </ul>
      <ul class="contact__list contact__list--address">
        <li>A : Your Address Here</li>
        <li>R. No. 05 P.O. 5400, BD</li>
      </ul>
    </div>
  </section>

</main>
</body>
</html>
```